Stillpeak website development

Need a website designed for a coaching business. Very high-end, luxury, professionalism, in the area of STRESS, see brief attached. I have a logo already
Updates

Slow in providing feedback

Target Market(s)

CEOs very successful men and wealthy females, high end luxury market

Industry/Entity Type

coaching

Number of Pages Required

1 page

Requirements
Must have
• Luxury look, professional, serious but warm, appealing to both sexes

```html
<!DOCTYPE html>
<html lang="en">
<head>
<meta charset="utf-8">
<title>Stillpeak – Lifestyle Coaching</title>
<link href="https://fonts.googleapis.com/css2?family=Fjalla+One&family=Roboto:wght@400;500;700&display=swap" rel="stylesheet">
<style>
:root{
  --navy:#0c2456;
  --navy-deep:#0a1f4a;
  --orange:#f47f20;
  --ink:#1b1b1b;
  --text:#555a63;
  --muted:#f0f1f4;
  --footer:#141519;
  --white:#fff;
}
*{margin:0;padding:0;box-sizing:border-box}
html,body{width:1200px;height:2990px;overflow:hidden}
body{font-family:"Roboto",sans-serif;color:var(--text);background:var(--white);position:relative}
.abs{position:absolute}
.display{font-family:"Fjalla One",sans-serif;font-weight:400;text-transform:uppercase;color:var(--ink)}
.accent{color:var(--orange)}
.btn{position:absolute;display:flex;align-items:center;justify-content:center;font-weight:700;font-size:16px;border-radius:3px;text-transform:uppercase}
.btn-navy{background:var(--navy);color:var(--white)}
.btn-white{background:var(--white);color:var(--navy)}

/* header */
.site-header{top:0;left:0;width:1200px;height:94px;background:var(--white);z-index:3}
.nav a{position:absolute;top:38px;font-size:15.5px;font-weight:500;color:#4a4f57;text-decoration:none;text-transform:uppercase}
.nav a.active{color:var(--navy);font-weight:700}
.nav a.active::after{content:"";position:absolute;left:0;right:0;bottom:-9px;height:3px;background:var(--navy)}
.nav-divider{position:absolute;top:0;width:1px;height:94px;background:#e4e6ea}
.social{position:absolute;width:38px;height:38px;border-radius:50%;border:2px solid var(--navy)}
.social.filled{background:var(--navy)}
.brand-disc{left:490px;top:-55px;width:220px;height:220px;border-radius:50%;background:var(--white);z-index:4;text-align:center}
.brand-mark{position:absolute;left:86px;top:66px;width:48px;height:48px;background:#2c2c2c;border-radius:4px}
.brand-name{position:absolute;left:0;right:0;top:145px;font-family:"Fjalla One",sans-serif;font-size:21px;letter-spacing:3px;color:#2c2c2c}
.brand-tag{position:absolute;left:0;right:0;top:170px;font-size:8.5px;letter-spacing:2px;color:#555}

/* hero */
.hero{top:94px;left:0;width:1200px;height:601px;background:linear-gradient(90deg,#3d5560 0%,#5a6f55 30%,#8b7a5e 55%,#b48c6a 75%,#6b5a4c 100%)}
.hero h1{position:absolute;left:110px;top:200px;font-size:46px;color:var(--white)}
.hero p{position:absolute;left:111px;top:266px;width:420px;font-size:17.5px;line-height:26px;color:var(--white);font-weight:500}
.dots{position:absolute;left:562px;top:565px;display:flex;gap:6px}
.dots span{width:15px;height:15px;border-radius:50%;background:var(--white)}
.dots span.on{background:transparent;border:3px solid var(--white)}
.bar{left:0;width:1200px;height:7px}

/* welcome */
.welcome h2{position:absolute;left:0;width:1200px;top:790px;text-align:center;font-size:35px}
.welcome p{position:absolute;left:125px;width:950px;top:862px;text-align:center;font-size:14.5px;line-height:25px}

/* why */
.why{top:1127px;left:0;width:1200px;height:471px;background:linear-gradient(90deg,#4f6a45 0%,#8aa0a8 25%,#5d7b8e 42%,#173a6e 58%,var(--navy-deep) 100%)}
.why h2{position:absolute;left:646px;top:60px;font-size:40px;color:var(--white)}
.bullets{list-style:none;position:absolute}
.bullets li{position:relative;padding-left:37px;font-size:14.5px;line-height:24px;margin-bottom:15px;text-align:justify}
.bullets li::before{content:"";position:absolute;left:2px;top:6px;width:12px;height:12px;border-radius:2px;background:currentColor;transform:rotate(45deg)}
.why .bullets{left:646px;top:130px;width:443px;color:var(--white)}

/* benefits */
.benefits h2{position:absolute;left:110px;top:1705px;font-size:42px}
.benefits .bullets{left:111px;top:1785px;width:492px;color:var(--text)}
.benefits .bullets li::before{background:#333}
.hex-photo{left:671px;top:1683px;width:418px;height:490px}

/* testimonials */
.testimonials{top:2254px;left:0;width:1200px;height:403px;background:var(--muted)}
.testimonials h2{position:absolute;left:0;width:1200px;top:66px;text-align:center;font-size:35px}
.card{position:absolute;top:147px;width:313px;height:191px;background:var(--white);border-radius:6px;box-shadow:0 2px 8px rgba(0,0,0,.05)}
.avatar{position:absolute;left:15px;top:22px;width:66px;height:66px;border-radius:50%;border:2px solid #cfd3da;background:linear-gradient(160deg,#d9c2ac,#8d6e57)}
.card h3{position:absolute;left:97px;top:40px;font-size:16px;font-weight:700;color:var(--ink)}
.stars{position:absolute;left:97px;top:60px;font-size:11px;letter-spacing:1px;color:var(--orange)}
.quote{position:absolute;right:15px;top:32px;font-family:"Fjalla One",sans-serif;font-size:72px;line-height:60px;color:#d7dbe2}
.card p{position:absolute;left:15px;top:110px;width:284px;font-size:14px;line-height:23px;text-align:justify}

/* footer */
.footer{top:2664px;left:0;width:1200px;height:326px;background:var(--footer);color:#e8e9ec}
.footer h4{position:absolute;top:83px;font-size:17px;font-weight:700;color:var(--white)}
.news{position:absolute;left:111px;top:121px;width:403px;height:50px;background:var(--white);border-radius:3px;border:2px solid var(--white)}
.news span{position:absolute;left:15px;top:15px;font-size:14px;color:#666}
.news b{position:absolute;right:0;top:0;width:107px;height:46px;background:var(--navy);color:var(--white);font-size:15px;display:flex;align-items:center;justify-content:center}
.links{position:absolute;left:563px;top:116px;list-style:none}
.links li{position:relative;padding-left:35px;font-size:15.5px;height:27.5px}
.links li::before{content:"";position:absolute;left:2px;top:5px;width:10px;height:10px;border-radius:2px;background:#e8e9ec;transform:rotate(45deg)}
.contact{position:absolute;left:857px;top:116px;width:240px;list-style:none}
.contact li{position:relative;padding-left:35px;font-size:15.5px;line-height:26px;margin-bottom:4px}
.contact svg{position:absolute;left:0;top:6px}
.rule{position:absolute;left:111px;top:271px;width:978px;height:1px;background:#3a3c42}
.copy{position:absolute;left:0;width:1200px;top:288px;text-align:center;font-size:14px}
.fsocial{position:absolute;top:281px;width:33px;height:33px;border-radius:50%;background:#23252b}
.fsocial.filled{background:var(--navy)}
</style>
</head>
<body>

<header class="site-header abs">
  <nav class="nav">
    <a class="active" style="left:110px">Home</a>
    <span class="nav-divider" style="left:177px"></span>
    <a style="left:200px">About</a>
    <span class="nav-divider" style="left:273px"></span>
    <a style="left:296px">Why Stillpeak</a>
    <a style="left:749px">Benefits</a>
    <span class="nav-divider" style="left:842px"></span>
    <a style="left:865px">Contact</a>
  </nav>
  <span class="social filled" style="left:967px;top:28px"></span>
  <span class="social" style="left:1009px;top:28px"></span>
  <span class="social" style="left:1050px;top:28px"></span>
</header>

<div class="brand-disc abs">
  <span class="brand-mark"></span>
  <div class="brand-name">STILLPEAK</div>
  <div class="brand-tag">— LIFESTYLE COACHING —</div>
</div>

<section class="hero abs" role="img" aria-label="Woman with long hair holding a white mug near her face, cliffside and sea in the background">
  <h1 class="display">Head Coach</h1>
  <p>Not your typical “quiet whale music playing in the background, kind of “stress guy”….stress is good</p>
  <span class="btn btn-navy" style="left:111px;top:342px;width:103px;height:50px">Men</span>
  <span class="btn btn-white" style="left:222px;top:342px;width:103px;height:50px">Women</span>
  <div class="dots"><span></span><span class="on"></span><span></span><span></span></div>
</section>
<svg class="abs bar" style="top:695px" width="1200" height="7"><polygon points="0,0 848,0 841,7 0,7" fill="#0c2456"/><polygon points="852,0 1200,0 1200,7 845,7" fill="#f47f20"/></svg>

<section class="welcome">
  <h2 class="display"><span class="accent">Welcome to</span> Stillpeak</h2>
  <p>Stillpeak came about due to my desire to help people lead a better and healthier life. Initially, I was involved in the fitness/body side of health. As years passed and my experience grew, I realized how important the mind was in total wellness, and that the mind is all powerful and controlling. Control the mind, control the body and achieve success. Stress can be the most debilitating factor in our lives, it is the root cause of so many diseases and costs the US workplace an estimated 300 billion dollars due to loss of productivity.</p>
  <span class="btn btn-navy" style="left:531px;top:997px;width:138px;height:50px">Learn More</span>
</section>

<section class="why abs" role="img" aria-label="Woman seated in a yoga pose facing misty green mountains, fading into a deep navy panel">
  <h2 class="display">Why Me?</h2>
  <ul class="bullets">
    <li>Been there done that! Have been through a lot, started businesses, selling a business, law suits, marriage, divorce, second marriage, kids, school, sports, fights, robbed, gun in face, traveled the world, successful, two great kids (both Cadets at Ridgeview Academy... duty/ honor/ country)</li>
    <li>Limited number of clients...different stage of life, empty nester, have a full career...won’t be a number</li>
  </ul>
  <span class="btn btn-white" style="left:646px;top:358px;width:138px;height:50px">Learn More</span>
</section>

<section class="benefits">
  <h2 class="display">Our <span class="accent">Benefits</span></h2>
  <ul class="bullets">
    <li>Sector expert Health/Wellness. Presented at numerous industry shows and quoted in national publications (not as a coach, I’m new, but in the health &amp; wellness space)</li>
    <li>Excellent listener...being in sales for many years, the secret is to really listen...and get to the end game, and make it feel as if it was their decision. Not sure how to word this as a benefit.</li>
    <li>Access/resources industry professionals, sport psychologist...just spent a few hours with the Mind performance coach for the Harbor Hawks baseball team...I can get the best advice and latest techniques in mind/body training performance.</li>
  </ul>
  <span class="btn btn-navy" style="left:111px;top:2086px;width:138px;height:50px">Learn More</span>
  <svg class="abs hex-photo" viewBox="0 0 418 490" role="img" aria-label="Smiling couple relaxing at a spa with candles and towels">
    <defs><linearGradient id="spa" x1="0" y1="0" x2="1" y2="1"><stop offset="0" stop-color="#f1ece4"/><stop offset=".5" stop-color="#d6b49a"/><stop offset="1" stop-color="#efe9e1"/></linearGradient></defs>
    <polygon points="209,0 418,115 418,375 209,490 0,375 0,115" fill="url(#spa)"/>
    <polyline points="0,375 209,490 418,375" fill="none" stroke="#0c2456" stroke-width="8"/>
  </svg>
</section>

<section class="testimonials abs">
  <h2 class="display"><span class="accent">What is</span> our clients say</h2>
  <div class="card" style="left:111px"><span class="avatar" role="img" aria-label="Client portrait"></span><h3>JOHN SMITH</h3><span class="stars">★★★★★</span><span class="quote">”</span><p>At vero eos et accusamus et iusto odio digni ssimos duci lormus qui blanditiis praesentium voluptatum delenitiea.</p></div>
  <div class="card" style="left:444px"><span class="avatar" role="img" aria-label="Client portrait"></span><h3>JOHN SMITH</h3><span class="stars">★★★★★</span><span class="quote">”</span><p>At vero eos et accusamus et iusto odio digni ssimos duci lormus qui blanditiis praesentium voluptatum delenitiea.</p></div>
  <div class="card" style="left:776px"><span class="avatar" role="img" aria-label="Client portrait"></span><h3>JOHN SMITH</h3><span class="stars">★★★★★</span><span class="quote">”</span><p>At vero eos et accusamus et iusto odio digni ssimos duci lormus qui blanditiis praesentium voluptatum delenitiea.</p></div>
</section>
<svg class="abs bar" style="top:2657px" width="1200" height="7"><polygon points="0,0 362,0 355,7 0,7" fill="#f47f20"/><polygon points="366,0 1200,0 1200,7 359,7" fill="#0c2456"/></svg>

<footer class="footer abs">
  <h4 style="left:111px">SUBSCRIBE OUR NEWSLETTER</h4>
  <div class="news"><span>Email Address</span><b>SIGN UP</b></div>
  <h4 style="left:563px">QUICK LINKS</h4>
  <ul class="links"><li>Home</li><li>About</li><li>Why Stillpeak</li><li>Benefits</li><li>Contact</li></ul>
  <h4 style="left:857px">CONTACT</h4>
  <ul class="contact">
    <li><svg width="12" height="15" viewBox="0 0 12 15"><path d="M6 0a6 6 0 0 0-6 6c0 4.5 6 9 6 9s6-4.5 6-9a6 6 0 0 0-6-6zm0 8.5A2.5 2.5 0 1 1 6 3.5a2.5 2.5 0 0 1 0 5z" fill="#e8e9ec"/></svg>465, Lorum Ipsum Dolore Sit, United States</li>
    <li><svg width="14" height="14" viewBox="0 0 14 14"><path d="M3 0l2.5 3.5-1.5 2a8 8 0 0 0 4.5 4.5l2-1.5L14 11l-1.5 2.5C6 14 0 8 .5 1.5z" fill="#e8e9ec"/></svg>+1 (888) 888 8888</li>
    <li><svg width="15" height="12" viewBox="0 0 15 12"><rect width="15" height="12" rx="1.5" fill="#e8e9ec"/><path d="M1 1.5l6.5 5 6.5-5" stroke="#141519" stroke-width="1.5" fill="none"/></svg>info@stillpeakcoach.com</li>
  </ul>
  <div class="rule"></div>
  <div class="copy">© 2022 STILLPEAK &nbsp;|&nbsp; All Rights Reserved &nbsp;|&nbsp; Privacy Policy</div>
  <span class="fsocial filled" style="left:983px"></span>
  <span class="fsocial" style="left:1019px"></span>
  <span class="fsocial" style="left:1056px"></span>
</footer>

</body>
</html>
```